Every Shelf Set Neatly or ESN Organized needs a business card design. ESN Organized is a professi

We need a business card design that is clean, sharp and conveys a sense of organization. I already have a logo.

Target Market(s)

Families (specifically mothers), small business owners, parents, seniors

Industry/Entity Type

Business

Contact Information for Business Card

My website is www.esnorganized-example.com and my Facebook page is http://www.sociallink-example.com/everyshelfsetneatly. The phone number is 418-552-7094 and I want to be listed as Lorna M. Pelham, Owner

Requirements
Must have
• My logo.

```html
<!DOCTYPE html>
<html lang="en">
<head>
<meta charset="utf-8">
<title>ESN Organized — Business Card</title>
<link rel="stylesheet" href="https://fonts.googleapis.com/css2?family=Questrial&display=swap">
<style>
  :root {
    --stage: #e9e6e1;
    --card-black: #0b0b0c;
    --card-sheen: #2a2b2e;
    --brand-blue: #3a8ad0;
    --band-blue-light: #4a98d8;
    --band-blue-dark: #2f78bd;
    --ink-white: #f4f6f8;
  }
  * { margin: 0; padding: 0; box-sizing: border-box; }
  html, body {
    width: 1200px;
    height: 1022px;
    overflow: hidden;
    background: var(--stage);
  }
  .stage {
    position: relative;
    width: 1200px;
    height: 1022px;
    display: flex;
    align-items: center;
    justify-content: center;
  }
  .business-card {
    position: relative;
    width: 960px;
    height: 548px;
    background: linear-gradient(115deg, var(--card-black) 0%, var(--card-sheen) 38%, var(--card-black) 62%, var(--card-black) 100%);
    border-radius: 4px;
    box-shadow: 0 18px 40px rgba(0, 0, 0, 0.25);
    overflow: hidden;
    font-family: "Questrial", "Helvetica Neue", Arial, sans-serif;
    color: var(--ink-white);
  }
  .brand-lockup {
    position: absolute;
    left: 70px;
    top: 128px;
    display: flex;
    align-items: flex-end;
    gap: 22px;
  }
  .brand-mark {
    display: flex;
    align-items: center;
    gap: 12px;
    font-size: 96px;
    line-height: 1;
    color: var(--brand-blue);
    letter-spacing: 2px;
  }
  .brand-mark-dot {
    width: 16px;
    height: 16px;
    border-radius: 50%;
    background: var(--brand-blue);
  }
  .brand-wordmark {
    display: flex;
    flex-direction: column;
    padding-bottom: 6px;
  }
  .brand-tagline {
    font-size: 30px;
    letter-spacing: 6px;
    line-height: 1.1;
  }
  .brand-name {
    font-size: 64px;
    letter-spacing: 16px;
    line-height: 1;
  }
  .owner-block {
    position: absolute;
    right: 60px;
    top: 282px;
    text-align: right;
  }
  .owner-name {
    font-size: 36px;
    color: var(--brand-blue);
    line-height: 1.1;
  }
  .owner-title {
    font-size: 22px;
    line-height: 1.2;
  }
  .contact-band {
    position: absolute;
    left: 0;
    right: 0;
    bottom: 0;
    height: 166px;
    background: linear-gradient(180deg, var(--band-blue-light), var(--band-blue-dark));
    padding: 28px 0 0 96px;
  }
  .contact-list { list-style: none; }
  .contact-item {
    display: flex;
    align-items: center;
    gap: 14px;
    font-size: 25px;
    line-height: 36px;
  }
  .contact-icon {
    width: 20px;
    height: 20px;
    flex: none;
  }
</style>
</head>
<body>
<main class="stage">
  <article class="business-card">
    <div class="brand-lockup">
      <div class="brand-mark">
        <span class="brand-mark-text">ESN</span>
        <span class="brand-mark-dot"></span>
      </div>
      <div class="brand-wordmark">
        <span class="brand-tagline">Every Shelf Set Neatly</span>
        <span class="brand-name">ORGANIZED</span>
      </div>
    </div>

    <div class="owner-block">
      <p class="owner-name">Lorna M. Pelham</p>
      <p class="owner-title">Owner</p>
    </div>

    <section class="contact-band">
      <ul class="contact-list">
        <li class="contact-item">
          <svg class="contact-icon" viewBox="0 0 24 24" aria-hidden="true">
            <path fill="#0c2a44" d="M6.6 10.8a15.1 15.1 0 0 0 6.6 6.6l2.2-2.2a1 1 0 0 1 1-.25 11.4 11.4 0 0 0 3.6.57 1 1 0 0 1 1 1V20a1 1 0 0 1-1 1A17 17 0 0 1 3 4a1 1 0 0 1 1-1h3.5a1 1 0 0 1 1 1c0 1.25.2 2.45.57 3.57a1 1 0 0 1-.25 1z"/>
          </svg>
          <span>418-552-7094</span>
        </li>
        <li class="contact-item">
          <svg class="contact-icon" viewBox="0 0 24 24" aria-hidden="true">
            <g fill="none" stroke="#0c2a44" stroke-width="2">
              <circle cx="12" cy="12" r="9"/>
              <ellipse cx="12" cy="12" rx="4" ry="9"/>
              <path d="M3 12h18M5 7h14M5 17h14"/>
            </g>
          </svg>
          <span>www.esnorganized-example.com</span>
        </li>
        <li class="contact-item">
          <svg class="contact-icon" viewBox="0 0 24 24" aria-hidden="true">
            <circle cx="12" cy="12" r="8" fill="#0c2a44"/>
          </svg>
          <span>www.sociallink-example.com/everyshelfsetneatly</span>
        </li>
      </ul>
    </section>
  </article>
</main>
</body>
</html>
```